Mobile Disc Jockey Service Brochure

We are looking for a brochure to showcase our Mobile DJ Business. It needs to be something professional looking and fit our target market of Weddings. We cater to events of all types but majority of our clients are brides looking for professional service at affordable prices.

Our website for reference: http://www.theclefcart.com/
facebook for reference: https://www.facebook.com/MarcusClefCart

I've uploaded a picture of us, our logo and some other photos that might be useful. Feel free to use additional stock photos that may be applicable to our project needs. Feel free to crop photos as necessary

I'd like this to be an 8 1/2" x 11" bifold, or trifold brochure, double sided. The front can be simple with our logo and phone number. Back can also be simple with a small logo and our website. I'd like one of the areas to focus on our bio and picture, and the other areas can describe our packages and what we offer as well as our mission statement

Some other information: We provide not only Professional and Enthusiastic DJ Services but we also do Uplighting as well as Event planning.

Target Market(s)

Weddings, Anniversary Parties, Birthdays, Themed Party

Industry/Entity Type

Business

Requirements
Must have
• Something describing our services like the following (feel free to rearrange the wording if necessary).
• All packages are hourly and custom built to fit your party needs. A list of our offerings includes:
• Cocktail music, dinner music, dance music
• Ultimate coordination of activities and unique event planning experience
• HD Sound
• LED Light Show
• Wireless Microphone System
• Unlimited choice of song titles from Digital to Vinyl
• Free travel within 50 miles - Travel outside of this is calculated with a fee per additional mile.
• Optional Services:
• Projector with Screen for Slide Shows & Movies
• Uplighting
• We provide a Fun & Easy to use web interface that walks you through the timeline of your event capturing every detail you desire, making planning fun! We guarantee you will hear everything you want, we have an endless music library as well as mobile internet so we can access any song you and your guests want instantly! In addition to the Online Event Planner, we offer unlimited consultations prior to your event to ensure face to face that you are getting everything you want and more.
• I'd like to see something featuring our services as well as our picture that I uploaded maybe cropped at the chest level or there abouts with this information:
• We are a husband and wife team. Marcus Holloway, the DJ has been providing custom soundtracks for events of all types for well over a decade. In 2011 his wife Tessa joined the team to handle all of the event coordination and logistics. Together we run the Clef Cart offering Professional DJ Services at a personal level. We enjoy working with clients to create the event that they deserve at an affordable price. Contact us today for your quote or visit us online.
• (555) 314-2286
• theclefcart@mailvo.com
• www.theclefcart.com
• www.facebook.com/MarcusClefCart
• Id also like something along the lines of:
• Your choice of DJ can make or break your event. The Clef Cart guarantees to go above and beyond to make your event flawless and unforgettable. We promise to provide nothing but the best, well within your budget. When it comes to Weddings, we recognize that your Wedding is the most important day of your life! We will work with you side by side to ensure that it's everything you have dreamed of and more. Let the experience we provide create a beautiful memory that will last a lifetime.
• (Mission Statement)
• Our mission is to provide high quality and affordable mobile DJ services that will fill your event with beautiful lifelong memories.
Nice to have
• Id like to see the picture of the bride and grandfather dancing put in there somewhere.
• Color Scheme should be a mix of greys, black, white, you can add color as needed to match photos/logo, etc.

```html
<!DOCTYPE html>
<html lang="en">
<head>
<meta charset="utf-8">
<title>The Clef Cart – Bifold Brochure</title>
<link rel="stylesheet" href="https://fonts.googleapis.com/css2?family=Didact+Gothic&family=Montserrat:wght@600&family=Arimo&display=swap">
<style>
  :root {
    --brand-red: #bd1400;
    --panel-grey: #e4e4e4;
    --paper: #ffffff;
    --ink: #222222;
    --on-red: #ffffff;
    --icon-gold: #f5b21b;
    --icon-navy: #1d2f6b;
    --icon-pink: #e8457a;
  }
  * { margin: 0; padding: 0; box-sizing: border-box; }
  html, body { width: 1200px; height: 1000px; overflow: hidden; background: var(--paper); }
  body { position: relative; font-family: "Didact Gothic", "Century Gothic", sans-serif; color: var(--ink); }

  .sheet-art { position: absolute; left: 0; top: 0; }

  .section-heading {
    position: absolute; left: 102px; top: 265px;
    font-family: "Montserrat", sans-serif; font-weight: 600; color: var(--on-red);
    line-height: 1.1;
  }
  .section-heading .eyebrow { display: block; font-size: 12px; }
  .section-heading .title { display: block; font-size: 17px; }

  .bio-copy {
    position: absolute; left: 102px; top: 343px; width: 190px;
    font-size: 10px; line-height: 11.5px;
  }
  .bio-copy p { margin-bottom: 6px; }

  .brand-name {
    position: absolute; display: flex; align-items: center; gap: 8px;
    color: var(--brand-red); white-space: nowrap;
  }
  .brand-name .dot { border-radius: 50%; background: var(--brand-red); flex: none; }
  .brand-name.is-small { left: 446px; top: 610px; font-size: 16px; }
  .brand-name.is-small .dot { width: 12px; height: 12px; }
  .brand-name.is-large { left: 778px; top: 490px; font-size: 34px; }
  .brand-name.is-large .dot { width: 26px; height: 26px; }

  .contact-block {
    position: absolute; right: 651px; top: 717px; text-align: right;
    color: var(--on-red);
  }
  .contact-block .invite { font-size: 11.5px; line-height: 14px; margin-bottom: 9px; }
  .contact-block .details { font-size: 9.2px; line-height: 11.5px; margin-bottom: 8px; }
  .contact-block .social { font-size: 10.3px; display: flex; align-items: center; justify-content: flex-end; gap: 5px; }
  .contact-block .social .square { width: 12px; height: 12px; background: var(--on-red); }

  .service-row { position: absolute; left: 818px; top: 716px; width: 320px; color: var(--on-red); }
  .service-labels { position: absolute; top: 63px; left: 0; width: 320px; font-size: 12px; }
  .service-labels span { position: absolute; white-space: nowrap; }
  .service-note { position: absolute; top: 81px; left: 10px; font-size: 10.8px; white-space: nowrap; }

  .panel-caption {
    position: absolute; top: 857px; font-family: "Arimo", sans-serif; font-size: 17px; color: #111;
  }
</style>
</head>
<body>

<svg class="sheet-art" width="1200" height="1000" viewBox="0 0 1200 1000" aria-hidden="true">
  <g class="panel-back">
    <polygon fill="var(--brand-red)" points="51,123 578,123 258,309 51,309"/>
    <polygon fill="var(--panel-grey)" points="262,324 600,129 600,518"/>
    <polygon fill="var(--panel-grey)" points="51,518 325,676 51,833"/>
    <polygon fill="var(--brand-red)" points="346,676 600,676 600,833 71,833"/>
  </g>
  <g class="panel-front">
    <polygon fill="var(--brand-red)" points="600,123 1127,123 807,309 600,309"/>
    <polygon fill="var(--panel-grey)" points="828,316 1149,131 1149,495"/>
    <polygon fill="var(--panel-grey)" points="600,518 874,676 600,833"/>
    <polygon fill="var(--brand-red)" points="895,676 1149,676 1149,833 620,833"/>
  </g>
  <g class="service-icons">
    <rect x="846" y="716" width="44" height="52" rx="4" fill="var(--icon-gold)" role="img" aria-label="DJ services illustration"/>
    <line x1="911" y1="720" x2="911" y2="790" stroke="#fff" stroke-width="2"/>
    <circle cx="958" cy="744" r="24" fill="var(--icon-navy)" role="img" aria-label="Uplighting illustration"/>
    <line x1="1006" y1="720" x2="1006" y2="790" stroke="#fff" stroke-width="2"/>
    <rect x="1047" y="720" width="44" height="44" rx="4" fill="var(--icon-pink)" role="img" aria-label="Event planning illustration"/>
  </g>
</svg>

<h2 class="section-heading"><span class="eyebrow">OUR</span><span class="title">BIODATA</span></h2>

<div class="bio-copy">
  <p>The Clef Cart provides Professional DJ services for metro Riverton and the surrounding areas. From weddings to parties of any kind, we will go above and beyond to provide your event with a memorable soundtrack!</p>
  <p>Planning your big event can be stressful so why not let us use our expertise and help make your event unforgettable! With professional equipment, lighting and a variety of custom packages available we have what you want and need!</p>
  <p>With a large library of songs, we are guaranteed to have everything you and your guests want to hear! Music is our passion and we look forward to sharing that at your next event!</p>
  <p>We are a husband and wife team. Marcus Holloway, the DJ has been providing custom sound tracks for events of all types for well over a decade. In 2011 his wife Tessa joined the team to handle all of the event coordination and logistics. Together we run the Clef Cart offering Professional DJ Services at a personal level. We enjoy working with clients to create the event that they deserve at an affordable price.</p>
</div>

<div class="brand-name is-small"><span class="dot"></span>The Clef Cart</div>

<div class="contact-block">
  <p class="invite">Contact us today for your<br>quote or visit us online.</p>
  <p class="details">P: (555) 314-2286<br>E: theclefcart@mailvo.com<br>W: www.theclefcart.com</p>
  <p class="social"><span class="square"></span>www.friendspace.com/MarcusClefCart</p>
</div>

<div class="brand-name is-large"><span class="dot"></span>The Clef Cart</div>

<div class="service-row">
  <div class="service-labels">
    <span style="left:9px">DJ SERVICES</span>
    <span style="left:109px">UPLIGHTING</span>
    <span style="left:206px">EVENT PLANNING</span>
  </div>
  <p class="service-note">All packages are hourly and custom built to fit your party needs</p>
</div>

<p class="panel-caption" style="left:270px">Option 1_Back</p>
<p class="panel-caption" style="left:818px">Option 1_Front</p>

</body>
</html>
```